Social Media Graphics - Oakline Push REVISED

Create 6-7 individual social media graphics (square size) to encourage folks to join our online course called:

The Harvest Ledger Circle
How to Launch a Multi-Million Business From Scratch
Sign Up Today!

IMPORTANT: Make the largest and most prominent text on the graphic be: How to Launch a Multi-Million Business From Scratch

For the color scheme of the graphics, let's try a blue color palette; make sure the graphics appeal to both men and women

Make sure each graphic contains 1 of the 3 pics attached (crop pic as needed); and make sure one of the graphics is all TEXT only.

Target Market(s)

men and women looking to start a business

Industry/Entity Type

Entrepreneurship

Colors
0054AA
0677BA
7BADD7
CADEEF
E8F1F8

Requirements
Must have
• All the text and use the 3 pics provided; one graphic can be all text; Simple, modern design that's easy to read

```html
<!DOCTYPE html>
<html lang="en">
<head>
<meta charset="UTF-8">
<title>The Harvest Ledger Circle – Sign Up</title>
<link rel="stylesheet" href="https://fonts.googleapis.com/css2?family=Archivo+Black&display=swap">
<style>
  :root {
    --blue-deep: #07479a;
    --blue-main: #0054AA;
    --blue-mid: #0677BA;
    --blue-soft: #7BADD7;
    --blue-pale: #CADEEF;
    --blue-mist: #E8F1F8;
    --navy: #0c1a3a;
    --shadow: #0a2f63;
    --white: #ffffff;
  }
  * { margin: 0; padding: 0; box-sizing: border-box; }
  html, body {
    width: 1200px; height: 1200px; overflow: hidden;
    background: var(--blue-main);
  }
  .poster {
    position: relative;
    width: 1200px; height: 1200px;
    background: radial-gradient(ellipse at 50% 45%, var(--blue-mid) 0%, var(--blue-main) 60%, var(--blue-deep) 100%);
    font-family: "Archivo Black", "Arial Black", sans-serif;
    color: var(--white);
    overflow: hidden;
  }
  .poster__frame {
    position: absolute;
    inset: 16px;
    border: 3px solid var(--blue-soft);
    border-radius: 80px;
    opacity: .85;
    z-index: 4;
    pointer-events: none;
  }
  .poster__photo {
    position: absolute;
    left: 20px; right: 20px;
    top: 180px; height: 630px;
    background:
      radial-gradient(ellipse 46% 40% at 56% 52%, rgba(255,255,255,.95) 0%, rgba(232,241,248,.8) 45%, rgba(232,241,248,0) 100%),
      radial-gradient(ellipse 30% 45% at 34% 62%, rgba(26,62,120,.55) 0%, rgba(26,62,120,0) 100%),
      radial-gradient(ellipse 22% 50% at 58% 68%, rgba(150,160,175,.55) 0%, rgba(150,160,175,0) 100%),
      linear-gradient(to bottom, var(--blue-soft) 0%, var(--blue-pale) 30%, var(--blue-mist) 55%, var(--blue-pale) 78%, var(--blue-mid) 100%);
    -webkit-mask-image:
      linear-gradient(to bottom, transparent 0%, #000 16%, #000 88%, transparent 100%),
      linear-gradient(to right, transparent 0%, #000 10%, #000 90%, transparent 100%);
    -webkit-mask-composite: source-in;
    mask-image:
      linear-gradient(to bottom, transparent 0%, #000 16%, #000 88%, transparent 100%),
      linear-gradient(to right, transparent 0%, #000 10%, #000 90%, transparent 100%);
    mask-composite: intersect;
    z-index: 1;
  }
  .title {
    position: absolute;
    top: 54px; left: 0; right: 0;
    text-align: center;
    z-index: 3;
    line-height: 1;
    text-transform: uppercase;
  }
  .title__top {
    display: flex;
    justify-content: center;
    align-items: center;
    gap: 10px;
    font-size: 56px;
    letter-spacing: -1px;
  }
  .title__pill {
    background: var(--navy);
    border: 3px solid var(--white);
    border-radius: 18px;
    padding: 5px 16px 3px;
  }
  .title__main {
    margin-top: 10px;
    font-size: 90px;
    letter-spacing: -1px;
    color: var(--blue-mist);
    text-shadow: 4px 5px 0 var(--shadow);
  }
  .headline {
    position: absolute;
    left: 59px; right: 60px;
    top: 800px; height: 259px;
    background: var(--blue-main);
    border: 6px solid var(--navy);
    border-radius: 14px;
    z-index: 3;
    display: flex;
    align-items: center;
    justify-content: center;
    text-align: center;
  }
  .headline__text {
    font-size: 74px;
    line-height: 0.98;
    letter-spacing: -1px;
    text-transform: uppercase;
  }
  .cta {
    position: absolute;
    top: 1090px; left: 0; right: 0;
    text-align: center;
    font-size: 42px;
    line-height: 1;
    letter-spacing: 0;
    text-transform: uppercase;
    z-index: 3;
  }
</style>
</head>
<body>
  <main class="poster">
    <div class="poster__frame"></div>

    <header class="title">
      <div class="title__top">
        <span>The</span>
        <span class="title__pill">Harvest Ledger</span>
      </div>
      <div class="title__main">Circle</div>
    </header>

    <div class="poster__photo" role="img" aria-label="Photo: two smiling course hosts on a balcony, a woman in a navy blazer leaning on the rail and a man in a grey blazer speaking into a microphone, bright windows behind them"></div>

    <section class="headline">
      <h1 class="headline__text">How to Launch a<br>Multi-Million Business<br>From Scratch</h1>
    </section>

    <p class="cta">Sign Up Today!</p>
  </main>
</body>
</html>
```